Brightarc Orthodontics appointment card design

I need appointment cards/ business cards made. Front will be Logo, name, title, email, phone number and location (5263 Walnut Hollow Pkwy, Ste 412, Concord, NC 28027) . the back should have an appointment card (name, time, date) and also 3 addresses listed with a check box so we can check to which location they are going.
Dale Fenwick Orthodontics
- 6735 Orchard Street, Ste 514, Harrisburg, NC 28075
- 3647 Ridgeway Drive NE, Ste 810, Concord, NC 28025
- 2917 Thornbury Corporate Drive, Ste 605, Charlotte, NC 28277
Business card can be horizontal or vertical in Design.
I need to be able to edit it to update and add new employees

Requirements
Must have
• Front:
• - Logo
• - Name & Title (able to be edited)
• - phone (704-555-0186) & Email (need to be able to edit)
• - Address: 5263 Walnut Hollow Pkwy, Ste 412
• Concord, NC 28027
• Back:
• Appointment Card design:
• - Name, time, Date
• - 3 locations w/ a check box so the patient knows where to go:
• Dale Fenwick Orthodontics
• - 6735 Orchard Street, Ste 514, Harrisburg, NC 28075
• - 3647 Ridgeway Drive NE, Ste 810, Concord, NC 28025
• - 2917 Thornbury Corporate Drive, Ste 605, Charlotte, NC 28277

```html
<!DOCTYPE html>
<html lang="en">
<head>
<meta charset="utf-8">
<title>Brightarc Orthodontics – Business &amp; Appointment Card</title>
<link rel="stylesheet" href="https://fonts.googleapis.com/css2?family=Lato:wght@400;700&family=Oswald:wght@600&display=swap">
<style>
  :root {
    --page: #d6d6d6;
    --card: #262626;
    --brand-blue: #1b74c5;
    --ink-light: #e6e6e6;
    --ink-muted: #bdbdbd;
    --panel: #ffffff;
    --panel-ink: #1a1a1a;
  }
  * { box-sizing: border-box; margin: 0; padding: 0; }
  html, body { width: 1200px; height: 1200px; overflow: hidden; }
  body {
    background: var(--page);
    font-family: "Lato", sans-serif;
    position: relative;
  }
  .card {
    position: absolute;
    left: 150px;
    width: 900px;
    height: 514px;
    background: var(--card);
    box-shadow: 0 10px 30px rgba(0,0,0,.35);
    overflow: hidden;
  }
  .card--front { top: 62px; }
  .card--back { top: 626px; }

  /* Brand name */
  .brand {
    position: absolute;
    font-family: "Lato", sans-serif;
    font-weight: 700;
    font-size: 52px;
    line-height: 1;
    letter-spacing: .5px;
    white-space: nowrap;
  }
  .brand small {
    display: block;
    font-size: 22px;
    letter-spacing: 6px;
    margin-top: 8px;
    text-transform: uppercase;
  }
  .card--front .brand { left: 330px; top: 92px; color: var(--brand-blue); }
  .card--back .brand { left: 300px; top: 44px; color: #ffffff; }

  /* Front */
  .divider {
    position: absolute;
    left: 60px; right: 90px; top: 288px;
    height: 3px;
    background: var(--brand-blue);
  }
  .address {
    position: absolute;
    right: 90px; top: 312px;
    text-align: right;
    color: var(--ink-light);
    font-size: 19px;
    line-height: 1.35;
  }
  .person {
    position: absolute;
    left: 60px; top: 336px;
    padding-left: 26px;
  }
  .person::before {
    content: "";
    position: absolute; left: 0; top: 4px;
    width: 11px; height: 48px;
    border-radius: 3px;
    background: var(--brand-blue);
  }
  .person__name {
    font-family: "Oswald", sans-serif;
    font-weight: 600;
    font-size: 30px;
    line-height: 1;
    color: var(--brand-blue);
    text-transform: uppercase;
  }
  .person__title {
    color: var(--ink-light);
    font-size: 19px;
    margin-top: 4px;
  }
  .contacts {
    position: absolute;
    left: 60px; top: 414px;
    list-style: none;
    color: var(--ink-light);
    font-size: 19px;
    line-height: 1.3;
  }
  .contacts li { display: flex; align-items: center; gap: 14px; }
  .contacts svg { width: 15px; height: 15px; fill: var(--brand-blue); flex: none; }

  /* Back */
  .appointment {
    position: absolute;
    left: 70px; right: 50px; top: 196px; bottom: 36px;
    background: var(--panel);
    color: var(--panel-ink);
    padding: 22px 34px 18px;
    font-size: 18px;
  }
  .field-row { display: flex; align-items: flex-end; gap: 10px; margin-bottom: 14px; }
  .field-label { font-weight: 700; white-space: nowrap; }
  .field-line { flex: 1; border-bottom: 1.5px solid var(--panel-ink); height: 18px; }
  .locations { list-style: none; margin-top: 6px; line-height: 1.45; }
  .locations li { display: flex; align-items: center; gap: 12px; white-space: nowrap; }
  .locations .heading { font-weight: 700; }
  .box {
    width: 15px; height: 15px;
    border: 1.5px solid var(--panel-ink);
    flex: none;
  }
  .box--filled { background: var(--panel-ink); }
</style>
</head>
<body>

<section class="card card--front" aria-label="Business card front">
  <div class="brand">Brightarc<small>Orthodontics</small></div>
  <div class="divider"></div>
  <p class="address">5263 Walnut Hollow Pkwy,<br>Ste 412 - Concord, NC 28027</p>
  <div class="person">
    <p class="person__name">Marcus Hale</p>
    <p class="person__title">CEO / Manager</p>
  </div>
  <ul class="contacts">
    <li>
      <svg viewBox="0 0 24 24" aria-hidden="true"><path d="M6.6 10.8a15.1 15.1 0 0 0 6.6 6.6l2.2-2.2a1 1 0 0 1 1-.25 11.4 11.4 0 0 0 3.6.57 1 1 0 0 1 1 1V20a1 1 0 0 1-1 1A17 17 0 0 1 3 4a1 1 0 0 1 1-1h3.5a1 1 0 0 1 1 1c0 1.250.2 2.450.57 3.6a1 1 0 0 1-.25 1z"/></svg>
      +704-555-0186
    </li>
    <li>
      <svg viewBox="0 0 24 24" aria-hidden="true"><path d="M12 2a10 10 0 1 0 0 20 10 10 0 0 0 0-20zm6.9 6h-2.9a15.7 15.7 0 0 0-1.4-3.6A8 8 0 0 1 18.9 8zM12 4c.8 1.2 1.5 2.5 1.9 4h-3.8c.4-1.5 1.1-2.8 1.9-4zM4.3 14a8 8 0 0 1 0-4h3.4a16 16 0 0 0 0 4zm.8 2h2.9c.3 1.3.8 2.5 1.4 3.6A8 8 0 0 1 5.1 16zM8 8H5.1a8 8 0 0 1 4.3-3.6C8.8 5.5 8.3 6.7 8 8zm4 12c-.8-1.2-1.5-2.5-1.9-4h3.8c-.4 1.5-1.1 2.8-1.9 4zm2.3-6H9.7a14.7 14.7 0 0 1 0-4h4.6a14.7 14.7 0 0 1 0 4zm.3 5.6c.6-1.1 1.1-2.3 1.4-3.6h2.9a8 8 0 0 1-4.3 3.6zm1.7-5.6a16 16 0 0 0 0-4h3.4a8 8 0 0 1 0 4z"/></svg>
      www.yourwebsite.com
    </li>
    <li>
      <svg viewBox="0 0 24 24" aria-hidden="true"><path d="M2 5h20v14H2zm2 2v.5l8 5 8-5V7zm0 2.8V17h16V9.8l-8 5z"/></svg>
      yourmail@here.com
    </li>
  </ul>
</section>

<section class="card card--back" aria-label="Appointment card back">
  <div class="brand">Brightarc<small>Orthodontics</small></div>
  <div class="appointment">
    <div class="field-row"><span class="field-line"></span></div>
    <div class="field-row">
      <span class="field-label">Name :</span><span class="field-line"></span>
      <span class="field-label">Date :</span><span class="field-line"></span>
    </div>
    <div class="field-row">
      <span class="field-label">Time :</span><span class="field-line"></span>
    </div>
    <ul class="locations">
      <li class="heading"><span class="box box--filled"></span>Dale Fenwick Orthodontics :</li>
      <li><span class="box"></span>6735 Orchard Street, Ste 514, Harrisburg, NC 28075</li>
      <li><span class="box"></span>3647 Ridgeway Drive NE, Ste 810, Concord, NC 28025</li>
      <li><span class="box"></span>2917 Thornbury Corporate Drive, Ste 605, Charlotte, NC 28277</li>
    </ul>
  </div>
</section>

</body>
</html>
```